Business card por a urban DJ, up scale audience target

Need a sober design, modern, conservative colors but i can consider some options, y play rnb, hip hop, EDM and top40.

Business card for contact and personal info, double sided, use logo attrached please; im 42 so i need a card acording to my age an target audience.

Target Market(s)

Adult people, up scale audience

Industry/Entity Type

Music Download

Contact Information for Business Card

Cel (318) 4207265518 www.lumadrift.com

Requirements
Must have
• open mind
Nice to have
• open mind
Should not have
• DJ

```html
<!DOCTYPE html>
<html lang="en">
<head>
<meta charset="utf-8">
<title>Luma Drift — Business Card</title>
<link rel="stylesheet" href="https://fonts.googleapis.com/css2?family=Arimo:wght@400;700&display=swap">
<style>
  :root {
    --backdrop: #8c8c8c;
    --card-black: #000000;
    --card-white: #ffffff;
    --band-grey: #3a3a3a;
    --ink: #111111;
    --mark-grey: #2f2f2f;
  }
  * { margin: 0; padding: 0; box-sizing: border-box; }
  html, body {
    width: 992px; height: 1200px; overflow: hidden;
    background: var(--backdrop);
    font-family: "Arimo", Arial, sans-serif;
  }
  .card {
    position: absolute; left: 98px; width: 808px; height: 463px;
    background: var(--card-black); overflow: hidden;
  }
  .card--front { top: 102px; }
  .card--back { top: 623px; }
  .card__shape { position: absolute; inset: 0; width: 100%; height: 100%; }
  .brand-name {
    position: absolute; font-weight: 700; letter-spacing: 4px; line-height: 1;
  }
  .card--front .brand-name {
    left: 440px; top: 96px; width: 268px; text-align: center;
    font-size: 78px; color: var(--mark-grey);
  }
  .card--back .brand-name {
    left: 0; top: 180px; width: 808px; text-align: center;
    font-size: 104px; color: var(--card-white);
  }
  .identity { position: absolute; left: 42px; top: 224px; color: var(--ink); }
  .identity__name { font-size: 27px; font-weight: 700; line-height: 1.1; }
  .identity__role { font-size: 19px; margin-top: 6px; }
  .contacts {
    position: absolute; left: 42px; top: 314px; list-style: none; color: var(--ink);
  }
  .contacts__item {
    display: flex; align-items: center; height: 31.5px; font-size: 17.5px; letter-spacing: 0.3px;
  }
  .contacts__icon { width: 14px; height: 14px; margin-right: 20px; flex: none; }
</style>
</head>
<body>

<section class="card card--front">
  <svg class="card__shape" viewBox="0 0 808 463" preserveAspectRatio="none" aria-hidden="true">
    <path fill="var(--band-grey)" d="M0,190 C60,70 170,12 262,0 L808,0 L808,0 C772,230 670,420 505,463 L0,463 Z"/>
    <path fill="var(--card-white)" d="M0,222 C70,80 190,18 285,0 L808,0 C770,215 650,410 474,463 L0,463 Z"/>
  </svg>

  <div class="brand-name">LUMA</div>

  <div class="identity">
    <h1 class="identity__name">Marcus Delaney</h1>
    <p class="identity__role">Managing Director</p>
  </div>

  <ul class="contacts">
    <li class="contacts__item">
      <svg class="contacts__icon" viewBox="0 0 14 14" aria-hidden="true">
        <rect width="14" height="14" fill="var(--ink)"/>
        <path d="M3 5 Q7 2 11 5 L10 6 L8.5 5.2 L5.5 5.2 L4 6 Z M4 7 H10 V11 H4 Z" fill="#fff"/>
      </svg>
      (318) 4207265518
    </li>
    <li class="contacts__item">
      <svg class="contacts__icon" viewBox="0 0 14 14" aria-hidden="true">
        <rect width="14" height="14" fill="var(--ink)"/>
        <circle cx="7" cy="7" r="4.3" fill="none" stroke="#fff" stroke-width="1.2"/>
        <path d="M2.7 7 H11.3 M7 2.7 Q4.6 7 7 11.3 M7 2.7 Q9.4 7 7 11.3" fill="none" stroke="#fff" stroke-width="0.9"/>
      </svg>
      www.lumadrift.com
    </li>
    <li class="contacts__item">
      <svg class="contacts__icon" viewBox="0 0 14 14" aria-hidden="true">
        <rect width="14" height="14" fill="var(--ink)"/>
        <rect x="2.5" y="4" width="9" height="6.5" fill="none" stroke="#fff" stroke-width="1.1"/>
        <path d="M2.5 4 L7 7.8 L11.5 4" fill="none" stroke="#fff" stroke-width="1.1"/>
      </svg>
      info@lumadrift.com
    </li>
    <li class="contacts__item">
      <svg class="contacts__icon" viewBox="0 0 14 14" aria-hidden="true">
        <rect width="14" height="14" fill="var(--ink)"/>
        <path d="M7 12 C4.5 8.8 3.8 7.6 3.8 6 A3.2 3.2 0 0 1 10.2 6 C10.2 7.6 9.5 8.8 7 12 Z" fill="#fff"/>
        <circle cx="7" cy="6" r="1.2" fill="var(--ink)"/>
      </svg>
      48 Harlow St, Suite Brookfield MA 0172
    </li>
  </ul>
</section>

<section class="card card--back">
  <div class="brand-name">LUMA</div>
</section>

</body>
</html>
```